Business Card Design needed for start up company Halvora

In need of a new business card designed for a start up company based in Sydney, Halvora is a new start up innovative Company, our mission it to make property accessible for everyday Australian and to become the leading Real Estate platform in Australia. We want it to be fresh and clean.

Industry/Entity Type

Financial

Contact Information for Business Card

Section for Name
Section for Title

HALVORA - The Strength of Pooling
Mobile:
Direct:

Font styles to use
Sans Serif

Colors
33a6d7
0692cd
0255a3
ffffff

Requirements
Must have
• Logo, all business card details

```html
<!DOCTYPE html>
<html lang="en">
<head>
<meta charset="utf-8">
<title>Halvora Business Card</title>
<link rel="stylesheet" href="https://fonts.googleapis.com/css2?family=Lato:wght@400;700;900&display=swap">
<style>
  :root {
    --sky: #33a6d7;
    --azure: #2a9bd6;
    --navy: #1d4a80;
    --deep: #0255a3;
    --white: #ffffff;
    --stage: #e9ecef;
    --map: #22538a;
  }
  * { margin: 0; padding: 0; box-sizing: border-box; }
  html, body { width: 1200px; height: 880px; overflow: hidden; }
  body {
    background: var(--stage);
    font-family: "Lato", sans-serif;
    position: relative;
  }
  .card {
    position: absolute;
    width: 560px;
    height: 320px;
    overflow: hidden;
    box-shadow: 0 10px 30px rgba(0,0,0,0.18);
  }
  .card--back { left: 90px; top: 60px; background: var(--navy); }
  .card--front { left: 550px; top: 480px; background: var(--white); }

  .world-map {
    position: absolute;
    left: 70px; top: 40px;
    width: 420px; height: 240px;
    border-radius: 40% 50% 45% 55%;
    background: radial-gradient(ellipse at center, var(--map) 0%, rgba(34,83,138,0) 70%);
  }
  .brand {
    position: absolute;
    display: flex;
    align-items: center;
    gap: 14px;
  }
  .brand__dot {
    border-radius: 50%;
    background: var(--azure);
    flex: none;
  }
  .brand__name {
    font-weight: 900;
    letter-spacing: 1px;
    line-height: 1;
  }
  .card--back .brand { left: 90px; top: 120px; }
  .card--back .brand__dot { width: 80px; height: 80px; }
  .card--back .brand__name { color: var(--white); font-size: 54px; }

  .front__tab {
    position: absolute;
    left: 40px; top: 0;
    width: 62px; height: 44px;
    background: var(--navy);
  }
  .front__arc {
    position: absolute;
    left: 330px; top: -80px;
    width: 400px; height: 400px;
    border-radius: 50%;
    background: var(--azure);
  }
  .card--front .brand { left: 40px; top: 34px; }
  .card--front .brand__dot { width: 90px; height: 90px; }
  .card--front .brand__name { color: var(--navy); font-size: 46px; }

  .contact { position: absolute; left: 56px; top: 170px; color: var(--navy); }
  .contact__name { font-weight: 900; font-size: 20px; line-height: 1.1; }
  .contact__title { color: var(--azure); font-size: 14px; margin-bottom: 18px; }
  .contact__line {
    display: flex; align-items: center; gap: 8px;
    font-size: 16px; line-height: 1.35;
  }
  .contact__icon { width: 14px; height: 14px; flex: none; }
  .tagline {
    position: absolute; left: 56px; top: 278px;
    color: var(--navy); font-size: 14px; font-weight: 700;
  }
</style>
</head>
<body>
  <section class="card card--back" aria-label="Card back">
    <div class="world-map" role="img" aria-label="Faint world map in dark blue"></div>
    <div class="brand">
      <span class="brand__dot"></span>
      <span class="brand__name">HALVORA</span>
    </div>
  </section>

  <section class="card card--front" aria-label="Card front">
    <div class="front__arc"></div>
    <div class="front__tab"></div>
    <div class="brand">
      <span class="brand__dot"></span>
      <span class="brand__name">HALVORA</span>
    </div>
    <div class="contact">
      <p class="contact__name">Liam Carter</p>
      <p class="contact__title">Sales Extraordinaire</p>
      <p class="contact__line">
        <svg class="contact__icon" viewBox="0 0 14 14" aria-hidden="true"><rect width="14" height="14" rx="2" fill="#2a9bd6"/><rect x="4" y="2" width="6" height="10" rx="1" fill="#fff"/></svg>
        555.204.7713
      </p>
      <p class="contact__line">
        <svg class="contact__icon" viewBox="0 0 14 14" aria-hidden="true"><rect width="14" height="14" rx="2" fill="#2a9bd6"/><path d="M3 5h8l-1 6H4z" fill="#fff"/><rect x="3" y="3" width="8" height="1.5" fill="#fff"/></svg>
        555.204.7713
      </p>
    </div>
    <p class="tagline">HALVORA - The Strength of Pooling</p>
  </section>
</body>
</html>
```